Hardcore nerd needs to stand out in a sea of dull Defence business cards

Wombarra Devices is a new Australian consulting engineering company that turns research and theory into practical systems. No evangelistic fluff, just mathematics and physics into electronic and optical circuits for consumer products, scientific research or Defence applications.

We already have a recognised logo (provided) which is often dark blue/black on a light background but we're open to other combinations. (Us engineers tend to have limited aesthetic imagination :)

Some of our recent products have included:
* Instrumentation for electrical testing,
* Radar jammers,
* GPS antenna design,
* Satellite tracking systems,
* High power lasers

We're open to both single and double-sided designs - happy to be convinced either way.

P.S. Another group is working on the web page, so - alas - our web site is currently of no use for images/ideas...

Target Market(s)

Engineering managers,
Scientists

Contact Information for Business Card

Dr Colin Harte
R&D Engineer

colin@wombarradevices.com.au
0427 563 710

PO Box XXX (to be confirmed)
Kelsby ACT 2917
Australia

Font styles to use
Serif
Sans Serif

Colors

Designer to choose colors to be used in the design.

Requirements
Must have
• My contact details!
• I've had many (great) "bold and plain" designs submitted already, so feel free to be artistically creative :)
• Happy to take advice re fonts/colours/printability etc.
Nice to have
• I'm not sure if "lists" are more at home on a CV than a business card, but representative services include:
• Applied electromagnetics
• RF and high speed electronics
• Signal and image processing
• Electro-optical and laser systems
• Concept-to-prototype design services
• If you're considering double sided cards, then often measuring/alignment grids/rulers feature on the back of similar cards.
• e.g. https://www.veltranoptics.example/newgrouppage9.cfm?objectgroup_id=4183
• https://www.veltranoptics.example/newgrouppage9.cfm?objectgroup_ID=4185
• ..or even a "Smith chart" (google will return lots)
• Generic images to represent a capability might work - googling images associated with keyword for each of these areas might help:
• - "passive radar", "phased array", "fdtd", "vircator"
• RF and high speed electronic design
• - "smith chart", "microstrip circuits", "dimensioned drawing", "electronic schematic"
• - "dft", "iir filter"
• - "optical cavity". "laser energy level diagram"
• Background/watermarked images outlines/wireframes/schematics would probably look OK.
Should not have
• If a list of projects/services is provided, it is important not to make the client feel that this is "all" the company can do. Engineering design is a creative discipline (like graphics :)
• Please, no stock "military" snaps like planes, missiles, etc!

```html
<!DOCTYPE html>
<html lang="en">
<head>
<meta charset="utf-8">
<title>Wombarra Devices – Business Card</title>
<link rel="stylesheet" href="https://fonts.googleapis.com/css2?family=Montserrat:wght@400;500;700&display=swap">
<style>
  :root {
    --stage: #3a2f29;
    --paper: #fbfbfd;
    --navy: #1b2474;
    --navy-deep: #141a5c;
    --navy-bright: #2a3aa6;
    --white: #ffffff;
  }
  html, body {
    margin: 0;
    padding: 0;
    width: 1200px;
    height: 716px;
    overflow: hidden;
    background: var(--stage);
    font-family: "Montserrat", Arial, sans-serif;
  }
  .canvas {
    position: relative;
    width: 1200px;
    height: 716px;
    display: flex;
    align-items: center;
    justify-content: center;
    gap: 50px;
  }
  .card {
    position: relative;
    width: 520px;
    height: 297px;
    border-radius: 3px;
    overflow: hidden;
    box-shadow: 0 12px 30px rgba(0,0,0,0.45);
  }
  /* Front */
  .card--front {
    background: var(--paper);
    color: var(--navy);
    border-bottom: 4px solid var(--navy);
  }
  .brand {
    position: absolute;
    left: 40px;
    top: 112px;
    display: flex;
    align-items: center;
    gap: 10px;
  }
  .brand__dot {
    width: 34px;
    height: 34px;
    border-radius: 50%;
    background: var(--navy);
    flex: none;
  }
  .brand__name {
    font-weight: 700;
    font-size: 17px;
    line-height: 1.05;
    letter-spacing: 0.5px;
    text-transform: uppercase;
  }
  .divider {
    position: absolute;
    left: 250px;
    top: 88px;
    width: 1.5px;
    height: 118px;
    background: var(--navy);
  }
  .contact {
    position: absolute;
    left: 272px;
    top: 92px;
    font-size: 11.5px;
    line-height: 1.4;
  }
  .contact__name {
    font-weight: 700;
    font-size: 17px;
    text-transform: uppercase;
    margin: 0;
  }
  .contact__role {
    margin: 0 0 12px;
    font-weight: 500;
  }
  .contact__address { margin: 0 0 10px; }
  .contact__line {
    display: flex;
    align-items: center;
    gap: 6px;
    margin: 0;
  }
  .contact__line svg { width: 10px; height: 10px; fill: var(--navy); flex: none; }
  /* Back */
  .card--back {
    background: linear-gradient(160deg, var(--navy-deep) 0%, var(--navy) 55%, var(--navy-bright) 100%);
  }
  .card__texture {
    position: absolute;
    inset: 0;
    background: radial-gradient(ellipse at 80% 90%, rgba(70,90,210,0.35), transparent 60%);
  }
  .brand--reverse {
    left: 170px;
    top: 128px;
    color: var(--white);
  }
  .brand--reverse .brand__dot { background: var(--white); width: 40px; height: 40px; }
  .brand--reverse .brand__name { font-size: 20px; }
</style>
</head>
<body>
<main class="canvas">
  <section class="card card--front" aria-label="Business card front">
    <div class="brand">
      <span class="brand__dot"></span>
      <span class="brand__name">Wombarra<br>Devices</span>
    </div>
    <div class="divider"></div>
    <div class="contact">
      <p class="contact__name">Dr Colin Harte</p>
      <p class="contact__role">R&amp;D Engineer</p>
      <p class="contact__address">PO Box XXX<br>Kelsby ACT 2917, Australia</p>
      <p class="contact__line">
        <svg viewBox="0 0 10 10"><path d="M2 0.5 L3.6 0.5 L4.3 3 L3.2 3.8 Q4.2 6 6.2 6.8 L7 5.7 L9.5 6.4 L9.5 8 Q9.5 9.5 8 9.5 Q0.5 9 0.5 2 Q0.5 0.5 2 0.5Z"/></svg>
        0427 563 710
      </p>
      <p class="contact__line">
        <svg viewBox="0 0 10 10"><path d="M0.5 2 L9.5 2 L9.5 8.5 L0.5 8.5Z M1 2.5 L5 5.6 L9 2.5" fill="none" stroke="#1b2474" stroke-width="1"/></svg>
        colin@wombarradevices.com.au
      </p>
    </div>
  </section>

  <section class="card card--back" aria-label="Business card back">
    <div class="card__texture" role="img" aria-label="Tiled embossed repeat of the company mark in tonal blues"></div>
    <div class="brand brand--reverse">
      <span class="brand__dot"></span>
      <span class="brand__name">Wombarra<br>Devices</span>
    </div>
  </section>
</main>
</body>
</html>
```